Tessmar Fahrwerkstatt
Sehr angenehme zusammenarbeit nicht aufdringlich und genau auf die Wünsche eingegangen. Wir werde sicher noch mehr zusammen Arbeiten. Gruss Lukas Hegemann Inhaber Tessmar Fahrwerkstatt
Zielgruppe
Dinks und Kunden mit viel Erfolg und hohem Ausgabepotential.
Aufgabenstellung
Unsere Firma vertreibt Fahrzeuge im Luxusbereich hauptgebiet Valmerra aber auch andere Sportwagen. Was uns fehlt ist ein optischer Wiedererkennugswert. Deshalb hätten wir gerne ein Visitenkarten Design und Briefpapier Design. Später soll auch noch eine Webseite mit gleichem Wiedererkennungswert entstehen. " Roter Faden "

```html
<!DOCTYPE html>
<html lang="de">
<head>
<meta charset="utf-8">
<title>Tessmar Fahrwerkstatt – Visitenkarte</title>
<link rel="stylesheet" href="https://fonts.googleapis.com/css2?family=Tenor+Sans&family=Arimo:wght@400;700&display=swap">
<style>
  :root {
    --backdrop: #d6d6d4;
    --card: #ffffff;
    --night: #0e1217;
    --night-soft: #2a2f36;
    --sky: #6dcbed;
    --ink: #1b1b1b;
    --accent: #3fb6e6;
  }
  * { margin: 0; padding: 0; box-sizing: border-box; }
  html, body { width: 1200px; height: 910px; overflow: hidden; }
  body { background: var(--backdrop); position: relative; }

  .card {
    position: absolute;
    top: 99px;
    width: 460px;
    height: 712px;
    background: var(--card);
    box-shadow: 0 8px 22px rgba(0,0,0,0.28);
    overflow: hidden;
  }
  .card--front { left: 99px; }
  .card--back { left: 655px; }
  .card__art { position: absolute; inset: 0; width: 460px; height: 712px; display: block; }

  .brand { position: absolute; color: var(--night); font-family: "Tenor Sans", sans-serif; text-transform: uppercase; text-align: center; }
  .brand__dot { display: block; margin: 0 auto; border-radius: 50%; background: var(--night); }
  .brand__name { display: block; letter-spacing: 0.02em; }

  .card--front .brand { left: 0; width: 460px; top: 504px; }
  .card--front .brand__dot { width: 60px; height: 60px; margin-bottom: 34px; }
  .card--front .brand__name { font-size: 30px; line-height: 33px; }

  .card--back .brand { left: 58px; width: 166px; top: 265px; }
  .card--back .brand__dot { width: 34px; height: 34px; margin-bottom: 14px; }
  .card--back .brand__name { font-size: 16px; line-height: 19px; }

  .contact {
    position: absolute;
    left: 74px;
    top: 374px;
    font-family: "Arimo", sans-serif;
    font-size: 21px;
    line-height: 27px;
    color: var(--ink);
  }
  .contact__name { color: var(--accent); font-weight: 700; font-size: 22px; }
  .contact__group { margin-top: 26px; }
</style>
</head>
<body>

  <section class="card card--front" aria-label="Visitenkarte Vorderseite">
    <svg class="card__art" viewBox="0 0 460 712">
      <defs>
        <radialGradient id="photoFront" cx="0.6" cy="0.45" r="0.7">
          <stop offset="0" stop-color="#2a2f36"/>
          <stop offset="1" stop-color="#0e1217"/>
        </radialGradient>
      </defs>
      <rect x="0" y="0" width="460" height="500" fill="url(#photoFront)" role="img" aria-label="Foto: Scheinwerfer eines dunklen Sportwagens in Nahaufnahme"/>
      <path class="band" d="M0 431 Q230 486 460 427 L460 712 L0 712 Z" fill="#6dcbed"/>
      <path class="panel" d="M0 455 Q230 510 460 450 L460 712 L0 712 Z" fill="#ffffff"/>
      <path class="pointer" d="M298 468 L360 466 L330 498 Z" fill="#0e1217"/>
    </svg>
    <div class="brand">
      <span class="brand__dot"></span>
      <span class="brand__name">Tessmar</span>
      <span class="brand__name">Fahrwerkstatt</span>
    </div>
  </section>

  <section class="card card--back" aria-label="Visitenkarte Rückseite">
    <svg class="card__art" viewBox="0 0 460 712">
      <defs>
        <radialGradient id="photoBack" cx="0.6" cy="0.2" r="0.6">
          <stop offset="0" stop-color="#2a2f36"/>
          <stop offset="1" stop-color="#0e1217"/>
        </radialGradient>
      </defs>
      <rect x="0" y="0" width="460" height="240" fill="url(#photoBack)" role="img" aria-label="Foto: Scheinwerfer eines dunklen Sportwagens, Ausschnitt"/>
      <path class="band" d="M0 183 Q230 225 460 178 L460 712 L0 712 Z" fill="#6dcbed"/>
      <path class="panel" d="M0 206 Q230 250 460 200 L460 712 L0 712 Z" fill="#ffffff"/>
      <path class="pointer" d="M300 216 L356 212 L328 246 Z" fill="#0e1217"/>
    </svg>
    <div class="brand">
      <span class="brand__dot"></span>
      <span class="brand__name">Tessmar</span>
      <span class="brand__name">Fahrwerkstatt</span>
    </div>
    <div class="contact">
      <p class="contact__name">Jonas Feldhaus</p>
      <p>Inhaber</p>
      <div class="contact__group">
        <p>Lindenhofweg 14</p>
        <p>41263 Ebersfelde</p>
      </div>
      <div class="contact__group">
        <p>Tel: 0221.836 21 40</p>
        <p>Fax: 0221.836 21 43</p>
      </div>
      <div class="contact__group">
        <p>E-Mail: info@tessmar-fahrwerk.de</p>
        <p>Web: www.tessmar-fahrwerk.de</p>
      </div>
    </div>
  </section>

</body>
</html>
```